New Business Card for Web Design/Internet Marketing Company

Looking for a great looking new business card. We are a 10 year old web design, internet marketing and website management company that works mostly with small businesses.

Our new card needs to better match the colors and style of our website, be bold, extremely usable and slightly edgy.

Target Market(s)

Small/Medium businesses that have websites

Industry/Entity Type

Internet

Requirements
Must have
• Front and back design, full color, rounded corners please

Must use the colors/style of our website (JPG provided)

INFO FOR CARDS (as readable as possible please)
Mark Lenner
President/CEO
mark@trelvanmedia.example
Phone: 520-381-7459
Toll Free: 866-381-7459
Address: 4315 W. Calloway Ave. Ste. 140, Tucson, AZ 85792

THINGS I WANT TO PROMOTE (if there is room):
1. Our Website - www.trelvanmedia.example

2. Social Media
Twitter: @trelvanmedia
Facebook: www.facebook.com/trelvanmedia

3. Our Services
Web Design
Internet Marketing
Website Management

```html
<!DOCTYPE html>
<html lang="en">
<head>
<meta charset="utf-8">
<title>Trelvan Media – Business Card</title>
<link rel="stylesheet" href="https://fonts.googleapis.com/css2?family=Source+Sans+3:wght@400;600;700&display=swap">
<style>
  :root {
    --backdrop: #9a6640;
    --card-white: #ffffff;
    --brand-orange: #f28a3c;
    --brand-blue: #1d8fc4;
    --ink-gray: #555a5e;
    --soft-white: #ffffff;
    --muted-white: rgba(255,255,255,0.88);
  }
  * { margin: 0; padding: 0; box-sizing: border-box; }
  html, body {
    width: 1200px; height: 402px; overflow: hidden;
    background: var(--backdrop);
    font-family: "Source Sans 3", "Myriad Pro", Arial, sans-serif;
  }
  .canvas { position: relative; width: 1200px; height: 402px; }

  .card {
    position: absolute; top: 57px; height: 292px;
    border-radius: 6px; overflow: hidden;
  }
  .card-front { left: 61px; width: 521px; background: var(--card-white); }
  .card-back { left: 624px; width: 514px; background: var(--brand-orange); color: var(--soft-white); }

  /* front */
  .brand-name {
    position: absolute; left: 30px; top: 52px;
    font-size: 50px; font-weight: 700; color: var(--brand-orange);
    letter-spacing: -0.5px; line-height: 1;
  }
  .tagline {
    position: absolute; right: 60px; top: 110px;
    font-size: 17px; color: var(--ink-gray);
  }
  .accent-bar-left {
    position: absolute; left: 0; top: 168px; width: 5px; height: 124px;
    background: var(--brand-blue);
  }
  .contact-list {
    position: absolute; left: 28px; top: 172px; list-style: none;
    font-size: 13px; color: var(--ink-gray); line-height: 18px;
  }
  .contact-list li { display: flex; align-items: center; gap: 5px; }
  .contact-list svg { width: 10px; height: 10px; fill: var(--brand-blue); flex: none; }
  .address {
    position: absolute; left: 28px; top: 251px;
    font-size: 13px; color: var(--ink-gray); line-height: 18px; font-style: normal;
  }
  .person {
    position: absolute; right: 20px; top: 208px; text-align: right;
    color: var(--brand-blue);
  }
  .person-name { font-size: 17px; font-weight: 700; line-height: 1.2; }
  .person-title { font-size: 12.5px; }
  .accent-bar-right {
    position: absolute; right: 0; top: 205px; width: 5px; height: 48px;
    background: var(--brand-orange);
  }

  /* back */
  .back-brand {
    position: absolute; left: 20px; top: 128px; width: 220px; text-align: center;
    font-size: 34px; font-weight: 700; line-height: 1.05; color: var(--soft-white);
  }
  .social-list {
    position: absolute; left: 265px; top: 42px; list-style: none;
    font-size: 17px; line-height: 25px; color: var(--muted-white);
  }
  .social-list li { display: flex; align-items: center; gap: 8px; }
  .social-dot { width: 15px; height: 15px; background: var(--brand-blue); border-radius: 2px; }
  .services-heading {
    position: absolute; left: 265px; top: 115px;
    font-size: 27px; font-weight: 700;
  }
  .services-list {
    position: absolute; left: 265px; top: 167px; list-style: none;
    font-size: 22px; line-height: 31px; color: var(--muted-white);
  }
</style>
</head>
<body>
<main class="canvas">
  <section class="card card-front" aria-label="Card front">
    <div class="brand-name">Trelvan Media</div>
    <div class="tagline">Sites that work hard</div>

    <span class="accent-bar-left"></span>
    <ul class="contact-list">
      <li><svg viewBox="0 0 10 10"><path d="M2 0.5 L3.8 2.6 L2.9 3.7 Q4.2 6 6.3 7.1 L7.4 6.2 L9.5 8 L8.2 9.5 Q1.5 8 0.5 1.8 Z"/></svg>520-381-7459</li>
      <li><svg viewBox="0 0 10 10"><path d="M2 0.5 L3.8 2.6 L2.9 3.7 Q4.2 6 6.3 7.1 L7.4 6.2 L9.5 8 L8.2 9.5 Q1.5 8 0.5 1.8 Z"/></svg>866-381-7459</li>
      <li><svg viewBox="0 0 10 10"><path d="M0 2 H10 V8.5 H0 Z M0 2 L5 5.8 L10 2" stroke="#fff" stroke-width="0.8"/></svg>mark@trelvanmedia.example</li>
      <li><svg viewBox="0 0 10 10"><circle cx="5" cy="5" r="4.6"/><path d="M0.5 5 H9.5 M5 0.4 V9.6 M5 0.4 Q1.8 5 5 9.6 M5 0.4 Q8.2 5 5 9.6" stroke="#fff" stroke-width="0.7" fill="none"/></svg>www.trelvanmedia.example</li>
    </ul>
    <address class="address">4315 W. Calloway Ave. Ste. 140<br>Tucson, AZ 85792</address>

    <div class="person">
      <div class="person-name">Mark Lenner</div>
      <div class="person-title">President/CEO</div>
    </div>
    <span class="accent-bar-right"></span>
  </section>

  <section class="card card-back" aria-label="Card back">
    <div class="back-brand">Trelvan<br>Media</div>
    <ul class="social-list">
      <li><span class="social-dot"></span>@trelvanmedia</li>
      <li><span class="social-dot"></span>trelvanmedia</li>
    </ul>
    <h2 class="services-heading">Our Services</h2>
    <ul class="services-list">
      <li>Web Design</li>
      <li>Internet Marketing</li>
      <li>Website Management</li>
    </ul>
  </section>
</main>
</body>
</html>
```